6"x9" Postcard Mailer

A 6"x9" Postcard mailer targeted to forensic laboratories to advertise or mock forensic samples (https://veltrascience.example/products/mock-forensic-samples/).

Here is some copy, but we can modify if there is not enough space:

Headline:
Expedite Training, Validation, & R&D with Our Ready-to-Use Mock Samples

Bullet Points:

- Wide Variety of Sample Types: IRB-approved samples mimicking crime scene substances, including semen, hair, bone, saliva, blood, and vaginal epithelial cells.
- Diverse Scenarios: Simulate sexual assault and degraded samples for varied conditions.
- Custom Solutions: Tailored DNA quantities and concentrations to suit your lab's needs.

Use discount code TRAL47 for a 10% discount

```html
<!DOCTYPE html>
<html lang="en">
<head>
<meta charset="utf-8">
<title>Veltra Science – Mock Samples Postcard</title>
<link rel="stylesheet" href="https://fonts.googleapis.com/css2?family=Anton&family=Montserrat:wght@600;700;800&family=Roboto:wght@400;500&display=swap">
<style>
  :root {
    --brand-blue: #224d97;
    --brand-blue-dark: #1b3f80;
    --paper: #ffffff;
    --paper-soft: #f1f1f1;
    --ink: #1c1c1c;
    --stage: #d9d7d4;
    --photo-dark: #15171c;
    --photo-glove: #2a5fc8;
    --photo-surface: #e4e4e6;
  }
  * { box-sizing: border-box; margin: 0; padding: 0; }
  html, body { width: 1200px; height: 900px; overflow: hidden; }
  body {
    background: var(--stage);
    display: flex;
    flex-direction: column;
    align-items: center;
    justify-content: center;
    gap: 34px;
    font-family: "Roboto", Arial, sans-serif;
    color: var(--ink);
  }
  .postcard {
    width: 600px;
    height: 400px;
    background: var(--paper);
    position: relative;
    overflow: hidden;
    box-shadow: 0 6px 18px rgba(0,0,0,.12);
  }

  /* ---------- Front ---------- */
  .front__logo-band {
    position: absolute; left: 0; top: 0; width: 330px; height: 86px;
    background: var(--paper-soft);
    display: flex; align-items: center; padding-left: 30px; gap: 10px;
  }
  .brand-dot { width: 14px; height: 14px; border-radius: 50%; background: var(--brand-blue); }
  .brand-name {
    font-family: "Montserrat", sans-serif; font-weight: 700;
    font-size: 30px; color: var(--brand-blue); letter-spacing: -.3px;
  }
  .front__panel {
    position: absolute; left: 0; top: 86px; width: 330px; bottom: 0;
    background: var(--brand-blue);
    padding: 46px 24px 0 30px;
    color: var(--paper);
  }
  .headline {
    font-family: "Montserrat", sans-serif; font-weight: 700;
    font-size: 25px; line-height: 1.12; text-align: center;
  }
  .headline__pill {
    display: block; margin: 6px 0 8px;
    background: var(--paper); color: var(--brand-blue);
    border-radius: 14px; padding: 4px 0;
    font-family: "Montserrat", sans-serif; font-weight: 800;
    font-size: 14px; text-align: center; letter-spacing: .2px;
  }
  .headline__product {
    display: block;
    font-family: "Anton", sans-serif; font-size: 44px; line-height: 1;
    text-align: center; letter-spacing: -.5px; white-space: nowrap;
  }
  .front__photo {
    position: absolute; left: 330px; top: 0; right: 0; bottom: 0;
    background:
      radial-gradient(ellipse 60% 22% at 62% 92%, rgba(196,24,40,.35), transparent 70%),
      radial-gradient(ellipse 55% 40% at 45% 38%, var(--photo-glove), transparent 72%),
      linear-gradient(180deg, var(--photo-dark) 0%, #2a2e38 45%, var(--photo-surface) 80%);
  }

  /* ---------- Back ---------- */
  .back__content { position: absolute; left: 30px; top: 22px; width: 340px; }
  .feature { margin-bottom: 6px; }
  .feature__title {
    display: inline-block;
    background: var(--brand-blue); color: var(--paper);
    font-family: "Montserrat", sans-serif; font-weight: 700; font-size: 16px;
    padding: 3px 26px 3px 10px;
    clip-path: polygon(0 0, 100% 0, calc(100% - 14px) 100%, 0 100%);
  }
  .feature__text { font-size: 11px; line-height: 1.35; margin-top: 3px; padding-left: 6px; }
  .coupon { position: relative; width: 290px; height: 88px; margin: 10px 0 0 18px; color: var(--paper); }
  .coupon svg { position: absolute; inset: 0; }
  .coupon__body {
    position: absolute; inset: 0; display: flex; align-items: center; justify-content: center; gap: 16px;
  }
  .coupon__offer { text-align: center; line-height: 1; }
  .coupon__small { font-family: "Montserrat", sans-serif; font-weight: 600; font-size: 11px; }
  .coupon__big { font-family: "Anton", sans-serif; font-size: 34px; }
  .coupon__divider { width: 1.5px; height: 48px; background: var(--paper); }
  .coupon__code-label { font-size: 8px; font-weight: 500; letter-spacing: .4px; }
  .coupon__code { font-family: "Anton", sans-serif; font-size: 30px; line-height: 1; }
  .contacts { list-style: none; margin: 10px 0 0 24px; }
  .contacts li { display: flex; align-items: center; gap: 10px; font-size: 14px; line-height: 17px; margin-bottom: 3px; }
  .contacts svg { width: 13px; height: 13px; flex: none; }
</style>
</head>
<body>

  <section class="postcard postcard--front" aria-label="Postcard front">
    <div class="front__logo-band">
      <span class="brand-dot"></span>
      <span class="brand-name">Veltra Science</span>
    </div>
    <div class="front__panel">
      <h1 class="headline">
        Expedite Training<br>Validation &amp; R&amp;D
        <span class="headline__pill">WITH OUR READY-TO-USE</span>
        <span class="headline__product">MOCK SAMPLES</span>
      </h1>
    </div>
    <div class="front__photo" role="img" aria-label="Photo of a gloved hand swabbing a red stain on a white surface"></div>
  </section>

  <section class="postcard postcard--back" aria-label="Postcard back">
    <div class="back__content">
      <div class="feature">
        <h2 class="feature__title">Wide Variety of Sample Types:</h2>
        <p class="feature__text">IRB-approved samples mimicking crime scene substances, including semen, hair, bone, saliva, blood, and vaginal epithelial cells.</p>
      </div>
      <div class="feature">
        <h2 class="feature__title">Diverse Scenarios:</h2>
        <p class="feature__text">Simulate sexual assault and degraded samples for varied conditions.</p>
      </div>
      <div class="feature">
        <h2 class="feature__title">Custom Solutions:</h2>
        <p class="feature__text">Tailored DNA quantities and concentrations to suit your lab's needs.</p>
      </div>

      <div class="coupon">
        <svg viewBox="0 0 290 100" width="290" height="88" preserveAspectRatio="none" aria-hidden="true">
          <path d="M10 0 H280 A10 10 0 0 0 290 10 V38 A12 12 0 0 0 290 62 V90 A10 10 0 0 0 280 100 H10 A10 10 0 0 0 0 90 V62 A12 12 0 0 0 0 38 V10 A10 10 0 0 0 10 0 Z" fill="var(--brand-blue)"/>
          <rect x="9" y="8" width="272" height="84" rx="6" fill="none" stroke="#ffffff" stroke-width="1" stroke-dasharray="4 3" opacity=".85"/>
        </svg>
        <div class="coupon__body">
          <div class="coupon__offer">
            <div class="coupon__small">FOR A</div>
            <div class="coupon__big">10%</div>
            <div class="coupon__small">DISCOUNT</div>
          </div>
          <span class="coupon__divider"></span>
          <div class="coupon__offer">
            <div class="coupon__code-label">USE DISCOUNT CODE</div>
            <div class="coupon__code">TRAL47</div>
          </div>
        </div>
      </div>

      <ul class="contacts">
        <li>
          <svg viewBox="0 0 16 16" aria-hidden="true"><circle cx="8" cy="8" r="7" fill="none" stroke="var(--brand-blue)" stroke-width="1.5"/><path d="M1 8h14M8 1c-3 3.5-3 10.5 0 14M8 1c3 3.5 3 10.5 0 14" fill="none" stroke="var(--brand-blue)" stroke-width="1.2"/></svg>
          www.veltrascience.example
        </li>
        <li>
          <svg viewBox="0 0 16 16" aria-hidden="true"><path d="M3 1.5l3 .5 1 3.5-2 1.5c1 2 2.5 3.5 4.5 4.5l1.5-2 3.5 1 .5 3c-7 1-13-5-12-12z" fill="var(--brand-blue)"/></svg>
          +1 555 014 2290
        </li>
        <li>
          <svg viewBox="0 0 16 16" aria-hidden="true"><rect x="1" y="3" width="14" height="10" rx="1" fill="var(--brand-blue)"/><path d="M1.5 3.5L8 9l6.5-5.5" fill="none" stroke="#fff" stroke-width="1.2"/></svg>
          info@veltrascience.example
        </li>
      </ul>
    </div>
  </section>

</body>
</html>
```